Basic Commercial & Residential Real Estate Web Site

I need a basic website for a new real estate company that deals with both residential and commercial sales. It must be clean and professional. We sell homes, office buildings, farms, and ranches. It should feel crisp and clean.
I need a main page with my logo and links to commercial, residential, farm and land searches with contact data forms. Also incorporated would be a mls property search (IDX) form. I am in Northern California and the current site I posted is at www.tlvarden.com. I need the functionality of the links and the supporting pages. I do not have all the copy ready because I did not know what to expect.
Updates

Project Deadline Extended
Reason: I apologize, I am extremely busy and you all need more data to do a good job. All the designs are great so far and it is extremely difficult to choose at this point. I haven't given you enough data. I haver now uploaded some relevent photos (not very good) and edited the brief. I am looking for what I call the Landing or main page with some functionality built in to other pages which I also need. Example if you click on "Commercial" it should go to a page that discusses our commercial dept.......

I would like to thank all the designers for all their hard work and efforts, I wish I could reward you all.

Thanks again for your creative and professional designs.

Edwin

Target Market(s)

Corporate Execs for the Commercial Buildings
Homeowners/Families for the Homes and Farms
Upper end people for the land to build estates

Industry/Entity Type

Real Estate

Font styles to use
Sans Serif

Requirements
Must have
• Our Logo should be prominent, pronounced
Need contact data or button
Functional Page that links to other data pages
Must Have a "search for properties" feature
Must say "Commercial and Residential Representation"
Pictures of Commercial Building and Nice Home (Tradtional not contemporary)
Nice to have
• Individual Buttons or links to "Commercial, Residential, Farm/Ranch, Land"
Contact Data displayed
button that says "Maple Crest"-next to button is Maple Crest Logo-see www.maplecrest.bz
Links to "Buyers and "Sellers"
Links to Facebook, twitter,.....etc
Should not have
• 20+ story commercial buildings or ultra modern. See uploaded files of typical buildings for commercial.

```html
<!DOCTYPE html>
<html lang="en">
<head>
<meta charset="utf-8">
<title>Properties by Varden</title>
<link rel="stylesheet" href="https://fonts.googleapis.com/css2?family=Open+Sans:wght@400;600&family=Ubuntu:wght@400&display=swap">
<style>
  :root {
    --accent: #29a4de;
    --ink: #222222;
    --text: #6e6e6e;
    --muted: #8a8a8a;
    --navy: #1d2a7a;
    --panel-dark: #2d2d2d;
    --search-dark: #1e1e1e;
    --field-dark: #141414;
    --page: #ffffff;
    --fold: #d9d9d9;
    --fold-light: #efefef;
    --rule: #d4d4d4;
    --input: #ececec;
  }
  * { box-sizing: border-box; margin: 0; padding: 0; }
  html, body { width: 1117px; height: 1200px; overflow: hidden; }
  body {
    position: relative;
    background: var(--page);
    font-family: "Open Sans", sans-serif;
    color: var(--text);
  }
  .abs { position: absolute; }

  /* background folds */
  .fold { position: absolute; }
  .fold-hero { left: 0; top: 286px; width: 1117px; height: 230px;
    background: linear-gradient(180deg, var(--fold-light), var(--fold)); }
  .fold-mid { left: 0; top: 753px; width: 1117px; height: 112px;
    background: linear-gradient(180deg, var(--fold), var(--fold-light)); }
  .fold-low { left: 0; top: 1104px; width: 1117px; height: 96px;
    background: linear-gradient(180deg, var(--fold), var(--fold-light)); }

  /* header */
  .brand { left: 149px; top: 10px; color: var(--ink); font-weight: 400; line-height: 1; }
  .brand-top { display: block; font-size: 15px; letter-spacing: 1px; padding-left: 48px; }
  .brand-main { display: block; font-size: 40px; letter-spacing: 1px; margin-top: 2px; }
  .call { left: 862px; top: 36px; font-size: 10px; color: var(--navy); font-weight: 600; white-space: nowrap; }
  .nav-rule { left: 149px; top: 81px; width: 817px; height: 1px; background: var(--rule); }
  .nav-mark { left: 184px; top: 79px; width: 62px; height: 3px; background: var(--accent); }
  .nav { left: 149px; top: 95px; width: 817px; height: 20px; list-style: none; font-size: 10.5px; color: var(--muted); }
  .nav li { position: absolute; transform: translateX(-50%); white-space: nowrap; }
  .hero-top { left: 149px; top: 123px; width: 817px; height: 6px; background: #e2e2e2; }

  /* hero */
  .hero-photo { left: 149px; top: 129px; width: 817px; height: 330px;
    background: linear-gradient(180deg, #9ec6ec 0%, #c9dcef 22%, #d9cfc0 45%, #cfc3b0 70%, #bcc3b4 100%); }
  .hero-base { left: 149px; top: 459px; width: 817px; height: 5px; background: #fff; }
  .search { left: 645px; top: 129px; width: 321px; height: 330px; }
  .search-title { left: 741px; top: 210px; font-family: "Ubuntu", sans-serif; font-size: 17px; color: #e8e8e8; }
  .select { left: 737px; width: 175px; height: 27px; border-radius: 7px; background: var(--field-dark);
    color: #d8d8d8; font-size: 11px; padding: 6px 13px; }
  .select::after { content: ""; position: absolute; right: 13px; top: 12px;
    border-left: 3px solid transparent; border-right: 3px solid transparent; border-top: 4px solid #555; }
  .search-btn { left: 737px; top: 355px; width: 175px; height: 28px; border-radius: 6px; background: var(--accent);
    color: #d6eefa; font-size: 11px; text-align: center; line-height: 28px; }
  .arrow { width: 41px; height: 44px; background: #111; }

  /* features */
  .features { left: 132px; top: 515px; width: 857px; height: 238px; background: var(--page); }
  .feature { position: absolute; top: 575px; width: 185px; }
  .feature-icon { position: absolute; left: 0; top: 0; width: 42px; height: 42px; border-radius: 50%; background: var(--accent); }
  .feature-title { position: absolute; left: 61px; top: 9px; font-size: 16px; color: var(--accent); }
  .feature-text { position: absolute; left: 0; top: 57px; width: 185px; font-size: 11px; line-height: 13px; color: var(--text); }
  .feature-more { position: absolute; left: 0; top: 105px; font-size: 11px; color: var(--accent); }

  /* call to action */
  .cta { left: 130px; top: 755px; width: 859px; height: 80px; background: var(--panel-dark); }
  .cta-title { left: 212px; top: 787px; font-size: 13px; color: #e6e6e6; }
  .cta-sub { left: 212px; top: 808px; font-size: 10px; color: #cfcfcf; }
  .cta-btn { left: 778px; top: 791px; width: 127px; height: 27px; background: var(--accent); color: #fff;
    font-size: 10px; text-align: center; line-height: 27px; font-weight: 600; }

  /* footer */
  .footer { left: 127px; top: 865px; width: 862px; height: 239px; background: var(--page); }
  .foot-links { list-style: none; font-size: 11px; line-height: 20.5px; color: var(--text); }
  .foot-head { font-size: 11px; color: var(--text); }
  .post { font-size: 10.5px; line-height: 12.5px; width: 180px; color: var(--text); }
  .post a { color: var(--navy); text-decoration: none; }
  .post-date { font-size: 10px; color: var(--text); }
  .field { left: 573px; width: 147px; height: 20px; background: var(--input); border: 1px solid #cfcfcf;
    border-radius: 2px; font-size: 10px; color: #999; padding: 3px 10px; }
  .subscribe-btn { left: 573px; top: 998px; width: 147px; height: 20px; background: var(--accent); color: #fff;
    font-size: 10px; padding: 3px 10px; border-radius: 2px; }
  .contact-line { left: 805px; font-size: 10.5px; color: var(--text); }
  .contact-line svg { position: absolute; left: 0; top: 2px; }
  .contact-line span { position: absolute; left: 24px; top: 0; white-space: nowrap; }

  /* bottom bar */
  .bottom { left: 127px; top: 1128px; width: 862px; height: 72px; background: var(--page); }
  .social { top: 1160px; width: 18px; height: 18px; background: var(--accent); border-radius: 2px; }
  .copy { left: 751px; top: 1162px; font-size: 9.5px; color: var(--text); white-space: nowrap; }
</style>
</head>
<body>

  <div class="fold fold-hero"></div>
  <div class="fold fold-mid"></div>
  <div class="fold fold-low"></div>

  <header>
    <div class="abs brand">
      <span class="brand-top">PROPERTIES BY</span>
      <span class="brand-main">VARDEN</span>
    </div>
    <div class="abs call">Call us: (530) - 555 - 0148</div>
    <div class="abs nav-rule"></div>
    <div class="abs nav-mark"></div>
    <ul class="abs nav">
      <li style="left:67px">Home</li>
      <li style="left:156px">About</li>
      <li style="left:246px">Services</li>
      <li style="left:349px">Commercial</li>
      <li style="left:463px">Residential</li>
      <li style="left:561px">Farm</li>
      <li style="left:639px">Land</li>
      <li style="left:732px">Contact</li>
    </ul>
  </header>

  <section class="hero">
    <div class="abs hero-top"></div>
    <div class="abs hero-photo" role="img" aria-label="Photo of a traditional cream stucco estate home with terrace, pool and garden under a blue sky"></div>
    <svg class="abs search" viewBox="0 0 321 330" aria-hidden="true">
      <polygon points="93,0 321,0 321,330 0,330" fill="var(--search-dark)"/>
    </svg>
    <div class="abs search-title">I'M Looking for</div>
    <div class="abs select" style="top:241px">Home</div>
    <div class="abs select" style="top:280px">Location</div>
    <div class="abs select" style="top:319px">My Budget</div>
    <div class="abs search-btn">Search</div>
    <div class="abs hero-base"></div>

    <svg class="abs arrow" style="left:128px;top:274px" viewBox="0 0 41 44" aria-label="Previous">
      <rect width="41" height="44" fill="#111"/>
      <polyline points="23,16 17,22 23,28" fill="none" stroke="#fff" stroke-width="3"/>
    </svg>
    <svg class="abs arrow" style="left:944px;top:274px" viewBox="0 0 41 44" aria-label="Next">
      <rect width="41" height="44" fill="#111"/>
      <polyline points="18,16 24,22 18,28" fill="none" stroke="#fff" stroke-width="3"/>
    </svg>
  </section>

  <section class="abs features"></section>

  <div class="feature" style="left:158px">
    <svg class="feature-icon" viewBox="0 0 42 42" aria-hidden="true">
      <circle cx="21" cy="21" r="21" fill="var(--accent)"/>
      <polygon points="21,13 13,20 15,20 15,28 19,28 19,23 23,23 23,28 27,28 27,20 29,20" fill="#fff"/>
    </svg>
    <div class="feature-title">Residential</div>
    <p class="feature-text">Lorem ipsum dolor sit amet this is a sample text that should be replaced later.</p>
    <div class="feature-more">&lt;&lt; More</div>
  </div>

  <div class="feature" style="left:366px">
    <svg class="feature-icon" viewBox="0 0 42 42" aria-hidden="true">
      <circle cx="21" cy="21" r="21" fill="var(--accent)"/>
      <rect x="13" y="16" width="16" height="12" rx="2" fill="#fff"/>
      <rect x="18" y="13" width="6" height="4" rx="1" fill="none" stroke="#fff" stroke-width="1.5"/>
    </svg>
    <div class="feature-title">Commercial</div>
    <p class="feature-text">Lorem ipsum dolor sit amet this is a sample text that should be replaced later.</p>
    <div class="feature-more">&lt;&lt; More</div>
  </div>

  <div class="feature" style="left:577px">
    <svg class="feature-icon" viewBox="0 0 42 42" aria-hidden="true">
      <circle cx="21" cy="21" r="21" fill="var(--accent)"/>
      <rect x="21" y="13" width="6" height="7" fill="#fff"/>
      <path d="M12 22 H30 M12 25 H30 M14 28 H28" stroke="#fff" stroke-width="1.6"/>
    </svg>
    <div class="feature-title">Farm</div>
    <p class="feature-text">Lorem ipsum dolor sit amet this is a sample text that should be replaced later.</p>
    <div class="feature-more">&lt;&lt; More</div>
  </div>

  <div class="feature" style="left:787px">
    <svg class="feature-icon" viewBox="0 0 42 42" aria-hidden="true">
      <circle cx="21" cy="21" r="21" fill="var(--accent)"/>
      <circle cx="21" cy="16" r="3" fill="#fff"/>
      <polygon points="12,29 19,22 23,25 26,22 31,29" fill="#fff"/>
    </svg>
    <div class="feature-title">Land</div>
    <p class="feature-text">Lorem ipsum dolor sit amet this is a sample text that should be replaced later.</p>
    <div class="feature-more">&lt;&lt; More</div>
  </div>

  <section class="cta-band">
    <div class="abs cta"></div>
    <div class="abs cta-title">Lorem Ipsum dolor sit amet this is a sample text</div>
    <div class="abs cta-sub">Lorem ipsum dolor sit amet this is a sample text and it should be replaced later</div>
    <div class="abs cta-btn">Call To Action</div>
  </section>

  <footer>
    <div class="abs footer"></div>
    <ul class="abs foot-links" style="left:154px;top:917px">
      <li>About</li><li>Services</li><li>Residential</li><li>Land</li><li>Commercial</li>
    </ul>
    <ul class="abs foot-links" style="left:262px;top:917px">
      <li>Privacy</li><li>Terms</li>
    </ul>

    <div class="abs foot-head" style="left:364px;top:920px">Latest Post</div>
    <p class="abs post" style="left:364px;top:945px">Lorem ipsdum dolor sit amet this is a sample blog post lorem ipsum dolor sit amet <a>&lt;&lt;more</a></p>
    <div class="abs post-date" style="left:364px;top:990px">8/9/2013</div>
    <p class="abs post" style="left:364px;top:1013px">Lorem ipsdum dolor sit amet this is a sample blog post lorem ipsum dolor sit amet <a>&lt;&lt;more</a></p>
    <div class="abs post-date" style="left:364px;top:1059px">8/9/2013</div>

    <div class="abs foot-head" style="left:573px;top:920px;color:var(--muted)">Subscribe</div>
    <div class="abs field" style="top:948px">Name</div>
    <div class="abs field" style="top:973px">Email</div>
    <div class="abs subscribe-btn">Subscribe</div>

    <div class="abs foot-head" style="left:805px;top:920px">Contact</div>
    <div class="abs contact-line" style="top:944px">
      <svg width="12" height="11" viewBox="0 0 12 11" aria-hidden="true"><polygon points="6,0 0,5 2,5 2,11 10,11 10,5 12,5" fill="#555"/></svg>
      <span>Address, TL Varden</span>
    </div>
    <div class="abs contact-line" style="top:967px">
      <svg width="11" height="11" viewBox="0 0 11 11" aria-hidden="true"><path d="M1 1 L4 1 L5 4 L3.5 5 Q5 7.5 6 7.5 L7 6 L10 7 L10 10 Q4 10 1 1 Z" fill="#555"/></svg>
      <span>(530) - 555 - &nbsp;0148</span>
    </div>
    <div class="abs contact-line" style="top:990px">
      <svg width="12" height="10" viewBox="0 0 12 10" aria-hidden="true"><rect x="0.5" y="0.5" width="11" height="9" fill="none" stroke="#555"/><polyline points="0.5,0.5 6,5 11.5,0.5" fill="none" stroke="#555"/></svg>
      <span>info@tlvarden.com</span>
    </div>
  </footer>

  <div class="abs bottom"></div>
  <div class="abs social" style="left:158px" aria-label="Social link"></div>
  <div class="abs social" style="left:180px" aria-label="Social link"></div>
  <div class="abs social" style="left:202px" aria-label="Social link"></div>
  <div class="abs social" style="left:224px" aria-label="Social link"></div>
  <div class="abs social" style="left:246px" aria-label="Social link"></div>
  <div class="abs copy">Copyright @ 2014 TL VARDEN. All Right Reserved</div>

</body>
</html>
```